professional business card design

Business card design. Photos have been uploaded and i am open to the designer choosing which photos to use. Would like the card to be mostyly in a grey scale design with black, whites, silver & grey colours. I have added copy of our flyer as would like on the back side of card our services to be listed. Do not use any bright colurs such as blue red green or yellow. i need to be able to edit the phone number and naem in the final card design submitted.

Target Market(s)

Clients

Industry/Entity Type

earhmovibng and transport

Contact Information for Business Card

Director Name, address, email, phone number and services

Colors

Designer to choose only greyscale colors for use in the design.

Requirements
Should not have
• no yellow, red, blue or green

```html
<!DOCTYPE html>
<html lang="en">
<head>
<meta charset="UTF-8">
<title>Business Card – Front and Back</title>
<link href="https://fonts.googleapis.com/css2?family=Arimo:wght@400;700&display=swap" rel="stylesheet">
<style>
  :root {
    --canvas: #2a2a2a;
    --card-top: #1c1c1c;
    --card-bottom: #0b0b0b;
    --white: #ffffff;
    --silver: #d6d6d6;
    --grey: #9a9a9a;
    --rule: #5a5a5a;
  }
  * { box-sizing: border-box; margin: 0; padding: 0; }
  html, body {
    width: 1200px; height: 900px; overflow: hidden;
    background: var(--canvas);
    font-family: "Arimo", Arial, sans-serif;
    color: var(--white);
  }
  .sheet {
    width: 1200px; height: 900px;
    display: flex; flex-direction: column;
    align-items: center; justify-content: center; gap: 56px;
  }
  .card {
    position: relative;
    width: 640px; height: 366px;
    border-radius: 22px;
    overflow: hidden;
    background: radial-gradient(ellipse at 40% 35%, var(--card-top), var(--card-bottom) 75%);
  }
  .card__texture {
    position: absolute; inset: 0;
    background: linear-gradient(160deg, rgba(255,255,255,0.04), rgba(255,255,255,0) 60%);
  }

  /* Front */
  .front__brand {
    position: absolute; left: 40px; top: 0; bottom: 0; width: 250px;
    display: flex; align-items: center; gap: 12px;
    font-size: 26px; font-weight: 700; color: var(--silver); line-height: 1.1;
  }
  .front__brand-dot {
    width: 16px; height: 16px; border-radius: 50%;
    background: var(--silver); flex: none;
  }
  .front__divider {
    position: absolute; left: 300px; top: 70px; bottom: 70px;
    width: 1px; background: var(--rule);
  }
  .front__details {
    position: absolute; left: 330px; top: 84px; right: 30px;
  }
  .person__name { font-size: 22px; font-weight: 700; letter-spacing: 0.5px; }
  .person__name-last { color: var(--grey); }
  .person__role { font-size: 16px; color: var(--silver); margin-top: 2px; }
  .contact { list-style: none; margin-top: 18px; }
  .contact__item {
    display: flex; align-items: center; gap: 9px;
    font-size: 17px; color: var(--silver); margin-bottom: 5px;
  }
  .contact__item svg { width: 15px; height: 15px; flex: none; }
  .address { margin-top: 14px; font-size: 17px; color: var(--silver); line-height: 1.3; }

  /* Back */
  .back__inner { position: absolute; inset: 36px 40px; }
  .services__title {
    text-align: center; font-size: 24px; font-weight: 700; letter-spacing: 0.5px;
  }
  .services__columns {
    display: flex; justify-content: space-between; margin-top: 18px;
  }
  .services__list { list-style: none; }
  .services__item {
    display: flex; align-items: center; gap: 9px;
    font-size: 15.5px; color: var(--silver); margin-bottom: 4px;
  }
  .services__item::before {
    content: ""; width: 8px; height: 8px; border-radius: 50%;
    background: var(--white); flex: none;
  }
  .services__note {
    text-align: center; font-size: 14px; color: var(--silver); margin-top: 22px;
  }
  .services__cta {
    text-align: center; font-size: 18px; font-weight: 700; margin-top: 6px;
  }
</style>
</head>
<body>
<main class="sheet">

  <section class="card card--front">
    <div class="card__texture" role="img" aria-label="Fine dark hexagonal texture across the card"></div>
    <div class="front__brand"><span class="front__brand-dot"></span>Ridgeline Haulage</div>
    <div class="front__divider"></div>
    <div class="front__details">
      <p class="person__name">JONATHAN <span class="person__name-last">SMITH</span></p>
      <p class="person__role">Managing Director</p>
      <ul class="contact">
        <li class="contact__item">
          <svg viewBox="0 0 24 24" fill="#d6d6d6"><path d="M6.6 10.8a15 15 0 0 0 6.6 6.6l2.2-2.2a1 1 0 0 1 1-.25 11.4 11.4 0 0 0 3.6.57 1 1 0 0 1 1 1V20a1 1 0 0 1-1 1A17 17 0 0 1 3 4a1 1 0 0 1 1-1h3.5a1 1 0 0 1 1 1c0 1.25.2 2.45.57 3.6a1 1 0 0 1-.25 1z"/></svg>
          044-123 456 789
        </li>
        <li class="contact__item">
          <svg viewBox="0 0 24 24" fill="#d6d6d6"><path d="M2 5h20v14H2z M3 6l9 7 9-7" stroke="#111" stroke-width="1.4"/></svg>
          info@webname.com
        </li>
        <li class="contact__item">
          <svg viewBox="0 0 24 24" fill="none" stroke="#d6d6d6" stroke-width="2"><circle cx="12" cy="12" r="9.5"/><path d="M2.5 12h19M12 2.5c3 3 3 16 0 19M12 2.5c-3 3-3 16 0 19"/></svg>
          www.websitename.com
        </li>
      </ul>
      <p class="address">421, Address line goes here<br>45452,Country Name</p>
    </div>
  </section>

  <section class="card card--back">
    <div class="card__texture" role="img" aria-label="Fine dark hexagonal texture across the card"></div>
    <div class="back__inner">
      <h2 class="services__title">OUR SERVICES</h2>
      <div class="services__columns">
        <ul class="services__list">
          <li class="services__item">Over size loads/hot shot loads</li>
          <li class="services__item">Heavy vehicle recovery services</li>
          <li class="services__item">Potable water deliveries</li>
          <li class="services__item">Road building/mainttenance</li>
          <li class="services__item">Earthworks</li>
          <li class="services__item">Sand &amp; metal supply &amp; cartage</li>
        </ul>
        <ul class="services__list">
          <li class="services__item">Road train tippers</li>
          <li class="services__item">Road train tankers</li>
          <li class="services__item">Road train flat tops</li>
          <li class="services__item">Drop deck trailers</li>
          <li class="services__item">Mine site accredited</li>
          <li class="services__item">Equipment &amp; operators</li>
        </ul>
      </div>
      <p class="services__note">we offer a large range of services not listed.</p>
      <p class="services__cta">So call us today for a personalised quote to suit your needs.</p>
    </div>
  </section>

</main>
</body>
</html>
```